Sales and Marketing company needs website page graphics

We are redesigning our website and need graphics for the top of our solution pages. Currently you’ll see that there is one photo graphic with a differing color screen for each section. We’re looking for photo graphic designs that will represent each unique solution section (lead generation, prospecting, hiring) and fit within the overall website design. We will add the section title text to the photo graphic. This will be a total of 3 graphics.

This is a link to the working website redesign: http://trevindale.com/brunexatemp/
The content on the working redesign page is correct and will give you a good sense for how we talk about each solution. You’ll notice that the redesign is text heavy. We’ll work on that next.

Our current website is: www.brunexa.com
You’ll get a good sense for our designs on our blog: http://www.brunexa.com/blog

As a company, our goal is to help our clients get more customers. We do that through consulting, training and outsourced lead generation. Key words that describe us: flexible, responsive, and fun. (Although you don’t see that in our current website, hopefully it comes through more on our blog – and then on our new website!)

We will need the graphic design in high resolution formats. We will own the copyright and intellectual property.

North American companies that earn $750K - $85M in annual revenue selling to other businesses. Most are in the computer technology industry.

Business Service

Sans Serif

• Fit the design of the website.
• If there are people in the graphics, I like to see diversity: Asian,Black, Latin, Caucasian, men and women.
• Be creative, not like every other graphic you see on a website. We are a woman owned business and Marisol is well known. We don't want to feel generic. Potentially be something we can use elements of for other graphics.
• We really want your expertise and this is our first project with Artvoyle .
• We will insert the solution section text, so there wouldn't be the text unless it's part of the graphic design.

```html
<!DOCTYPE html>
<html lang="en">
<head>
<meta charset="utf-8">
<title>Brunexa – Sales Prospecting</title>
<link rel="stylesheet" href="https://fonts.googleapis.com/css2?family=Lato:wght@400;700&display=swap">
<style>
  :root {
    --purple: #5b3a93;
    --purple-dark: #4a2d7d;
    --purple-light: #7b5bb3;
    --green: #7cc242;
    --grey: #9a9a9a;
    --grey-light: #d9d9d9;
    --text: #444444;
    --white: #ffffff;
    --paper: rgba(255, 255, 255, 0.55);
    --device: rgba(120, 120, 130, 0.55);
    --accent-warm: rgba(240, 150, 90, 0.45);
    --page: #f4f5f7;
  }
  * { box-sizing: border-box; margin: 0; padding: 0; }
  html, body { width: 1200px; height: 758px; overflow: hidden; background: var(--page); }
  body { font-family: "Lato", Arial, sans-serif; color: var(--text); }

  .page { width: 1200px; height: 758px; background: var(--white); display: flex; flex-direction: column; }

  .site-header { height: 70px; flex: none; display: flex; align-items: center; padding: 0 40px 0 86px; }
  .brand { display: flex; align-items: center; gap: 10px; }
  .brand-name { font-size: 34px; font-weight: 700; color: var(--purple); letter-spacing: 0.5px; }
  .brand-mark { width: 20px; height: 20px; background: var(--purple); }
  .header-note { font-size: 12px; color: var(--purple); letter-spacing: 0.6px; margin-left: auto; margin-right: 150px; margin-top: 22px; }
  .header-phone { font-size: 20px; color: var(--purple); align-self: flex-start; margin-top: 18px; }

  .main-nav { height: 26px; flex: none; background: var(--purple); display: flex; justify-content: flex-end; padding-right: 40px; }
  .main-nav a { color: var(--white); text-decoration: none; font-size: 10px; text-transform: uppercase; letter-spacing: 0.6px; padding: 0 12px; line-height: 26px; }
  .main-nav a.is-active { background: var(--green); }

  .hero {
    height: 370px; flex: none;
    background:
      radial-gradient(ellipse 170px 120px at 62% 38%, var(--device), transparent 70%),
      radial-gradient(ellipse 110px 130px at 26% 48%, var(--paper), transparent 70%),
      radial-gradient(ellipse 70px 40px at 42% 18%, var(--paper), transparent 70%),
      radial-gradient(ellipse 90px 60px at 60% 78%, var(--accent-warm), transparent 70%),
      radial-gradient(ellipse 80px 50px at 22% 80%, var(--accent-warm), transparent 70%),
      linear-gradient(135deg, var(--purple-dark), var(--purple) 55%, var(--purple-light));
  }

  .content { flex: 1; display: flex; padding: 14px 60px 0 80px; gap: 34px; overflow: hidden; }
  .system-diagram { width: 230px; height: 190px; flex: none; }
  .article { flex: 1; font-size: 11px; line-height: 1.55; }
  .article h1 { font-size: 26px; font-weight: 400; color: var(--purple); margin-bottom: 6px; line-height: 1.2; }
  .article p { margin-bottom: 7px; }
  .article ul { margin: 0 0 7px 18px; }
  .article a { color: var(--purple); text-decoration: none; }
</style>
</head>
<body>
<div class="page">
  <header class="site-header">
    <div class="brand">
      <span class="brand-name">Brunexa</span>
      <span class="brand-mark"></span>
    </div>
    <span class="header-note">SEND REFERRALS TO OUR TEAM</span>
    <span class="header-phone">+1 555 0142</span>
  </header>

  <nav class="main-nav">
    <a href="#">About</a>
    <a href="#">What We Do</a>
    <a href="#">Lead Generation</a>
    <a href="#" class="is-active">Prospecting</a>
    <a href="#">Hiring Consultants</a>
    <a href="#">Resources</a>
    <a href="#">Events</a>
    <a href="#">Blog</a>
    <a href="#">Contact</a>
  </nav>

  <div class="hero" role="img" aria-label="Prospecting header illustration on purple: hands typing on a laptop at centre right, printed reports with bar and pie charts held at left, a calculator, glasses, a phone, a notepad and a pencil on the desk, all linked by thin white circuit lines"></div>

  <section class="content">
    <svg class="system-diagram" viewBox="0 0 250 200" aria-label="Revenue Generating System diagram">
      <circle cx="125" cy="100" r="72" fill="none" stroke="var(--grey-light)" stroke-width="10"/>
      <text x="125" y="96" text-anchor="middle" font-family="Lato, sans-serif" font-size="15" fill="var(--grey)">Revenue</text>
      <text x="125" y="114" text-anchor="middle" font-family="Lato, sans-serif" font-size="15" fill="var(--grey)">Generating</text>
      <text x="125" y="132" text-anchor="middle" font-family="Lato, sans-serif" font-size="15" fill="var(--grey)">System</text>
      <circle cx="125" cy="30" r="28" fill="var(--grey)"/>
      <text x="125" y="33" text-anchor="middle" font-family="Lato, sans-serif" font-size="7" fill="var(--white)">LEAD GEN</text>
      <circle cx="58" cy="150" r="28" fill="var(--purple)"/>
      <text x="58" y="153" text-anchor="middle" font-family="Lato, sans-serif" font-size="7" fill="var(--white)">PROSPECTING</text>
      <circle cx="192" cy="150" r="28" fill="var(--grey)"/>
      <text x="192" y="153" text-anchor="middle" font-family="Lato, sans-serif" font-size="7" fill="var(--white)">HIRING</text>
    </svg>

    <article class="article">
      <h1>The Brunexa Approach to Sales Prospecting</h1>
      <p>Sales is not magic. We believe that success is built on a clear process. It's a matter of giving your people:</p>
      <ul>
        <li>the right tools</li>
        <li>the right scripts and</li>
        <li>the right sales training</li>
      </ul>
      <p>At Brunexa we help your team build the skills and confidence to reach decision makers. Our prospecting program combines three proven elements to build sales confidence and grow your customers.</p>
      <p>Many leaders assume a great sales manager can solve cold calling on their own. It rarely works. The truth is that cold calling is only one part of a balanced development strategy. Our prospecting strategy combines a <a href="#">mix of prospect attraction strategies</a>: personal, digital, and collaborative.</p>
      <p>Sales people need a proven approach to make the first contact with confidence, build rapport and set quality meetings.</p>
    </article>
  </section>
</div>
</body>
</html>
```